Vorlanta PowerPoint Template

I have a company called Vorlanta, LLC and my company logo is already designed. I need a PowerPoint template that I will be using to pitch potential investors and business partners. This should be a very professional-looking template that leverages the company logo colors and really pops. The company is an AI product research and development company.

```html
<!DOCTYPE html>
<html lang="en">
<head>
<meta charset="utf-8">
<title>Vorlanta Pitch Template</title>
<link href="https://fonts.googleapis.com/css2?family=Poppins:wght@400;500;600;700&family=Roboto:wght@500;700&display=swap" rel="stylesheet">
<style>
:root{
  --red:#b3111c;
  --red-deep:#9c0c16;
  --red-soft:#e0484f;
  --ink:#2d2d2f;
  --bar:#3b3b3d;
  --paper:#ffffff;
  --paper-tint:#f5f5f7;
  --stage:#d5d5d7;
  --muted:#55565a;
}
*{box-sizing:border-box;margin:0;padding:0}
html,body{width:1026px;height:1200px;overflow:hidden;background:var(--stage)}
body{position:relative;font-family:"Poppins",sans-serif;color:var(--ink)}
.slide{position:absolute;width:443px;height:249px;overflow:hidden;background:var(--paper);box-shadow:0 8px 14px rgba(0,0,0,.18)}
.col-l{left:51px}.col-r{left:531px}
.row-1{top:54px}.row-2{top:335px}.row-3{top:616px}.row-4{top:897px}
.abs{position:absolute}
.brand{position:absolute;display:flex;align-items:center;gap:5px;font-family:"Poppins",sans-serif;font-weight:600;letter-spacing:-.5px;line-height:1}
.brand-dot{border-radius:50%;background:var(--red);flex:none}
.brand-name{color:var(--ink)}
.brand.on-red .brand-dot{background:#fff}
.brand.on-red .brand-name{color:#fff}
.brand.sm{font-size:20px}.brand.sm .brand-dot{width:22px;height:22px}
.heading{position:absolute;font-family:"Roboto",sans-serif;font-weight:700;font-size:15px;color:var(--ink);letter-spacing:.2px}
.heading em{font-style:normal;color:var(--red)}
.body-copy{position:absolute;font-size:5.2px;line-height:1.6;color:var(--muted);text-align:justify}
.footer{position:absolute;left:0;right:0;top:228px;height:17px;background:var(--bar);display:flex;align-items:center;padding-left:25px;font-size:5.6px;color:#fff;gap:6px}
.footer .ico{width:6px;height:6px;fill:var(--red)}
.footer.light{background:#fff;color:var(--ink)}
.page-no{position:absolute;right:26px;top:2px;width:13px;height:13px;border-radius:50%;background:#fff;border:1.5px solid var(--bar);font-size:5px;font-weight:700;color:var(--ink);display:flex;align-items:center;justify-content:center}
.top-stripe{position:absolute;top:0;left:0;height:4px;width:100%}
.photo{position:absolute}
.pill{position:absolute;left:25px;height:23px;border-radius:12px;background:#fff;box-shadow:0 2px 5px rgba(0,0,0,.14);display:flex;align-items:center;padding:0 9px 0 10px;justify-content:space-between;font-size:6.3px;font-weight:600;color:var(--ink)}
.arrow-dot{width:9px;height:9px;border-radius:50%;background:var(--red);display:flex;align-items:center;justify-content:center}
.arrow-dot svg{width:4px;height:4px}
.service-ico{position:absolute;width:32px;height:32px;border-radius:50%;background:var(--red);border:3px solid #fbe1e2;display:flex;align-items:center;justify-content:center}
.service-title{position:absolute;left:250px;font-size:6.4px;font-weight:700;color:var(--ink)}
.service-copy{position:absolute;left:250px;width:150px;font-size:5px;line-height:1.55;color:var(--muted);text-align:justify}
.year{position:absolute;width:101px;text-align:center;font-size:8px;font-weight:600;top:62px}
.stage-frame{position:absolute;top:82px;width:101px;height:101px;border:1px solid var(--red-soft)}
.stage-frame.dashed{border-style:dashed}
.stage-card{position:absolute;inset:8px;background:var(--red-soft);box-shadow:0 2px 4px rgba(0,0,0,.2);display:flex;flex-direction:column;align-items:center;justify-content:center;color:#fff;text-align:center;padding:0 5px}
.stage-card.deep{background:var(--red)}
.stage-card h4{font-size:5.6px;font-weight:700;margin:7px 0 3px}
.stage-card p{font-size:4.6px;line-height:1.6}
.value-list{position:absolute;left:26px;top:53px;width:180px;list-style:none}
.value-list li{position:relative;padding-left:11px;font-size:5.1px;line-height:1.6;color:var(--muted);margin-bottom:6.3px}
.value-list li::before{content:"";position:absolute;left:0;top:2px;width:4px;height:4px;border-radius:50%;border:1px solid var(--red)}
.contact-row{position:absolute;left:262px;display:flex;align-items:center;gap:9px;font-size:7.6px;font-weight:500;color:#fff;line-height:1.3}
.contact-ico{width:22px;height:22px;border-radius:50%;background:#fff;display:flex;align-items:center;justify-content:center;flex:none}
.contact-ico svg{width:9px;height:9px;fill:var(--ink)}
</style>
</head>
<body>

<section class="slide col-l row-1">
  <div class="photo" style="left:0;top:0;width:443px;height:190px;background:linear-gradient(120deg,#c9212c 0%,#a50f19 55%,#d43a44 100%)" role="img" aria-label="Red-tinted image of a robotic hand reaching toward a human hand over circuit lines"></div>
  <svg class="abs" style="left:0;top:0" width="443" height="249" viewBox="0 0 443 249">
    <path d="M0 178 C80 140 160 150 240 182 C320 208 390 180 443 162 L443 249 L0 249 Z" fill="#e9e9eb"/>
    <path d="M0 183 C80 146 160 156 240 188 C320 214 390 186 443 168 L443 249 L0 249 Z" fill="#fff"/>
  </svg>
  <div class="brand on-red" style="left:124px;top:68px;font-size:36px;gap:9px"><span class="brand-dot" style="width:42px;height:42px"></span><span class="brand-name">Vorlanta</span></div>
  <div class="abs" style="left:272px;top:126px;width:112px;height:112px;border-radius:50%;background:#fff;box-shadow:0 2px 6px rgba(0,0,0,.15)"></div>
  <div class="photo" style="left:278px;top:132px;width:100px;height:100px;border-radius:50%;background:radial-gradient(circle at 60% 40%,#b9b9bb,#4a4a4c)" role="img" aria-label="Black and white photo of a woman working on a laptop"></div>
  <div class="heading" style="left:26px;top:181px;font-size:16px;line-height:1.15">AI-DRIVEN PRODUCT<br><em>INNOVATION</em></div>
  <p class="body-copy" style="left:26px;top:221px;width:240px;font-size:5.8px;color:var(--ink);text-align:left">Sed ut perspiciatis unde omnis iste natus error sit voluptatem accusantium doloremque laudantium, totam rem apea.</p>
</section>

<section class="slide col-r row-1" style="background:var(--paper-tint)">
  <div class="brand sm" style="left:26px;top:21px;font-size:22px"><span class="brand-dot" style="width:25px;height:25px"></span><span class="brand-name">Vorlanta</span></div>
  <div class="heading" style="left:32px;top:63px;font-size:16px">AGENDA</div>
  <div class="pill" style="top:92px;width:133px">VISION &amp; MISSION<span class="arrow-dot"><svg viewBox="0 0 4 4"><path d="M1 .5L3 2 1 3.5" stroke="#fff" stroke-width=".8" fill="none"/></svg></span></div>
  <div class="pill" style="top:122px;width:149px">OUR SOLUTION<span class="arrow-dot"><svg viewBox="0 0 4 4"><path d="M1 .5L3 2 1 3.5" stroke="#fff" stroke-width=".8" fill="none"/></svg></span></div>
  <div class="pill" style="top:155px;width:181px">TECHNOLOGY DIFFERENTIATION<span class="arrow-dot"><svg viewBox="0 0 4 4"><path d="M1 .5L3 2 1 3.5" stroke="#fff" stroke-width=".8" fill="none"/></svg></span></div>
  <div class="pill" style="top:185px;width:149px">PRODUCT ROADMAP<span class="arrow-dot"><svg viewBox="0 0 4 4"><path d="M1 .5L3 2 1 3.5" stroke="#fff" stroke-width=".8" fill="none"/></svg></span></div>
  <svg class="abs" style="left:0;top:0" width="443" height="249"><polygon points="246,22 418,22 418,168" fill="var(--red)"/></svg>
  <div class="photo" style="left:264px;top:34px;width:142px;height:170px;background:linear-gradient(150deg,#0d2a3a,#1a4e66 55%,#0b1c26)" role="img" aria-label="Hands using a laptop with floating AI data dashboards"></div>
  <div class="footer"><svg class="ico" viewBox="0 0 10 10"><path d="M2 1l2 2-1 1.5a6 6 0 002.5 2.5L7 6l2 2-1.5 1.5C4 9 1 6 .5 2.5z"/></svg>+1 (555) 014 2278 &nbsp;|&nbsp; <svg class="ico" viewBox="0 0 10 10"><rect x="0" y="2" width="10" height="7"/></svg>info@vorlanta.com<span class="page-no">02</span></div>
</section>

<section class="slide col-l row-2">
  <svg class="abs" style="left:0;top:0" width="443" height="249" role="img" aria-label="Black and white photo of a businessman holding a tablet with AI network graphics">
    <defs><linearGradient id="aboutTone" x1="0" y1="0" x2="1" y2="1"><stop offset="0" stop-color="#6e6e70"/><stop offset="1" stop-color="#1e1e20"/></linearGradient></defs>
    <path d="M0 0 H188 A150 150 0 0 1 110 222 L0 222 Z" fill="url(#aboutTone)"/>
  </svg>
  <div class="abs" style="left:125px;top:133px;width:84px;height:84px;border-radius:50%;background:var(--red);border:5px solid #fff"></div>
  <div class="brand sm" style="left:314px;top:13px"><span class="brand-dot"></span><span class="brand-name">Vorlanta</span></div>
  <div class="heading" style="left:240px;top:51px;font-size:15px">ABOUT <em>US</em></div>
  <p class="abs" style="left:240px;top:72px;width:170px;font-size:7.8px;font-weight:500;color:var(--red);line-height:1.4">To empower the future with groundbreaking AI technologies that solve real-world problems.</p>
  <p class="body-copy" style="left:240px;top:111px;width:179px">Lorem ipsum dolor sit amet, consectetur adipiscing elit, sed do eiusmod tempor incididunt ut labore et dolore magna aliqua. Ut enim ad minim veniam, quis nostrud exercitation ullamco laboris nisi ut aliquip ex ea commodo consequat. Duis aute irure dolor in reprehenderit in voluptate velit esse cillum dolore eu fugiat nulla pariatur. Excepteur sint occaecat cupidatat non proident, sunt in culpa qui officia deserunt mollit anim id est laborum.</p>
  <p class="body-copy" style="left:240px;top:173px;width:179px">Lorem ipsum dolor sit amet, consectetur adipiscing elit, sed do eiusmod tempor incididunt ut labore et dolore magna aliqua. Ut enim ad minim veniamea.</p>
  <div class="footer"><svg class="ico" viewBox="0 0 10 10"><path d="M2 1l2 2-1 1.5a6 6 0 002.5 2.5L7 6l2 2-1.5 1.5C4 9 1 6 .5 2.5z"/></svg>+1 (555) 014 2278 &nbsp;|&nbsp; <svg class="ico" viewBox="0 0 10 10"><rect x="0" y="2" width="10" height="7"/></svg>info@vorlanta.com<span class="page-no">03</span></div>
</section>

<section class="slide col-r row-2" style="background:var(--paper-tint)">
  <svg class="top-stripe" viewBox="0 0 443 4" preserveAspectRatio="none"><polygon points="0,0 323,0 318,4 0,4" fill="var(--red)"/></svg>
  <div class="heading" style="left:26px;top:13px">OUR <em>SOLUTION</em></div>
  <div class="brand sm" style="left:314px;top:11px"><span class="brand-dot"></span><span class="brand-name">Vorlanta</span></div>
  <div class="abs" style="left:39px;top:51px;width:160px;height:160px;border-radius:50%;background:#dadadc"></div>
  <div class="photo" style="left:47px;top:59px;width:144px;height:144px;border-radius:50%;background:radial-gradient(circle at 60% 45%,#2f6f88,#0e2b3b)" role="img" aria-label="Hands typing on a laptop with chat bubbles and an AI head graphic"></div>
  <svg class="abs" style="left:0;top:0" width="443" height="249"><path d="M203 50 C245 80 250 180 203 210" fill="none" stroke="#444" stroke-width=".7" stroke-dasharray="1.5 2"/><circle cx="203" cy="50" r="1.5" fill="#444"/><circle cx="203" cy="210" r="1.5" fill="#444"/></svg>
  <div class="service-ico" style="left:207px;top:66px"><svg width="14" height="14" viewBox="0 0 14 14" fill="none" stroke="#fff" stroke-width="1"><circle cx="7" cy="6" r="4"/><path d="M5 10v3h4v-3"/></svg></div>
  <div class="service-ico" style="left:220px;top:115px"><svg width="14" height="14" viewBox="0 0 14 14" fill="none" stroke="#fff" stroke-width="1"><circle cx="7" cy="6" r="4.5"/><path d="M5 12h4M7 4v4"/></svg></div>
  <div class="service-ico" style="left:207px;top:163px"><svg width="14" height="14" viewBox="0 0 14 14" fill="none" stroke="#fff" stroke-width="1"><path d="M3 9a3 3 0 010-6 4 4 0 018 1 2.5 2.5 0 010 5z"/><path d="M5 9v3M7 9v4M9 9v3"/></svg></div>
  <div class="service-title" style="top:66px">RAPID AI PRODUCT PROTOTYPING</div>
  <p class="service-copy" style="top:77px">Lorem ipsum dolor sit amet, consectetur adipiscing elit, sed do eiusmod tempor incididunt ut labore et dolore magna enim ad minim veniamea.</p>
  <div class="service-title" style="top:114px;left:264px">INNOVATION-AS-A-SERVICE</div>
  <p class="service-copy" style="top:125px;left:264px">Lorem ipsum dolor sit amet, consectetur adipiscing elit, sed do eiusmod tempor incididunt ut labore et dolore magna enim ad minim veniamea.</p>
  <div class="service-title" style="top:163px">AI INFRASTRUCTURE CONSULTING</div>
  <p class="service-copy" style="top:174px">Lorem ipsum dolor sit amet, consectetur adipiscing elit, sed do eiusmod tempor incididunt ut labore et dolore magna enim ad minim veniamea.</p>
  <div class="footer"><svg class="ico" viewBox="0 0 10 10"><path d="M2 1l2 2-1 1.5a6 6 0 002.5 2.5L7 6l2 2-1.5 1.5C4 9 1 6 .5 2.5z"/></svg>+1 (555) 014 2278 &nbsp;|&nbsp; <svg class="ico" viewBox="0 0 10 10"><rect x="0" y="2" width="10" height="7"/></svg>info@vorlanta.com<span class="page-no">04</span></div>
</section>

<section class="slide col-l row-3" style="background:var(--red-deep)">
  <div class="photo" style="left:0;top:0;width:443px;height:228px;background:radial-gradient(circle at 50% 45%,#c62430,#a10d17 65%)" role="img" aria-label="Faint red background of a light bulb with circuit lines and business icons"></div>
  <div class="brand sm on-red" style="left:314px;top:11px"><span class="brand-dot"></span><span class="brand-name">Vorlanta</span></div>
  <div class="heading" style="left:0;width:443px;top:111px;text-align:center;font-size:25px;color:#fff;letter-spacing:.5px">SECTION DIVIDER</div>
  <div class="footer light" style="top:227px;height:13px"><svg class="ico" viewBox="0 0 10 10"><path d="M2 1l2 2-1 1.5a6 6 0 002.5 2.5L7 6l2 2-1.5 1.5C4 9 1 6 .5 2.5z"/></svg>+1 (555) 014 2278 &nbsp;|&nbsp; <svg class="ico" viewBox="0 0 10 10"><rect x="0" y="2" width="10" height="7"/></svg>info@vorlanta.com<span class="page-no" style="top:0;background:var(--bar);color:#fff;border-color:#fff">05</span></div>
</section>

<section class="slide col-r row-3" style="background:var(--paper-tint)">
  <svg class="top-stripe" viewBox="0 0 443 4" preserveAspectRatio="none"><polygon points="0,0 323,0 318,4 0,4" fill="var(--red)"/></svg>
  <div class="heading" style="left:26px;top:13px">PRODUCT <em>ROADMAP</em></div>
  <div class="brand sm" style="left:314px;top:11px"><span class="brand-dot"></span><span class="brand-name">Vorlanta</span></div>
  <div class="year" style="left:49px">2023</div>
  <div class="year" style="left:170px">2024</div>
  <div class="year" style="left:292px">2025</div>
  <div class="stage-frame" style="left:49px;border-style:solid dashed dashed dashed"><div class="stage-card"><svg width="16" height="14" viewBox="0 0 16 14" fill="none" stroke="#fff" stroke-width=".9"><rect x="1" y="1" width="11" height="9"/><circle cx="11" cy="9" r="3"/><path d="M13 11l2 2"/></svg><h4>ORIENTATION</h4><p>Sed ut perspiciatis unde omni iste natus error sit voluptatem accusantium.</p></div></div>
  <div class="stage-frame dashed" style="left:170px;border-style:dashed solid solid solid"><div class="stage-card deep"><svg width="16" height="14" viewBox="0 0 16 14" fill="none" stroke="#fff" stroke-width=".9"><rect x="3" y="1" width="10" height="8"/><path d="M1 12h14"/></svg><h4>STRATEGY</h4><p>Sed ut perspiciatis unde omni iste natus error sit voluptatem accusantium.</p></div></div>
  <div class="stage-frame" style="left:292px;border-style:solid dashed dashed dashed"><div class="stage-card deep"><svg width="16" height="14" viewBox="0 0 16 14" fill="none" stroke="#fff" stroke-width=".9"><rect x="1" y="3" width="9" height="10"/><circle cx="12" cy="4" r="2.5"/><path d="M3 6h5M3 9h5"/></svg><h4>IMPLEMENTATION</h4><p>Sed ut perspiciatis unde omni iste natus error sit voluptatem accusantium.</p></div></div>
  <svg class="abs" style="left:0;top:0" width="443" height="249"><path d="M150 132h18M271 132h19" stroke="var(--red-soft)" stroke-width=".8"/><path d="M166 130l3 2-3 2zM288 130l3 2-3 2z" fill="var(--red-soft)"/></svg>
  <div class="footer"><svg class="ico" viewBox="0 0 10 10"><path d="M2 1l2 2-1 1.5a6 6 0 002.5 2.5L7 6l2 2-1.5 1.5C4 9 1 6 .5 2.5z"/></svg>+1 (555) 014 2278 &nbsp;|&nbsp; <svg class="ico" viewBox="0 0 10 10"><rect x="0" y="2" width="10" height="7"/></svg>info@vorlanta.com<span class="page-no">06</span></div>
</section>

<section class="slide col-l row-4">
  <svg class="top-stripe" viewBox="0 0 443 4" preserveAspectRatio="none"><polygon points="0,0 323,0 318,4 0,4" fill="var(--red)"/></svg>
  <div class="heading" style="left:26px;top:13px">VALUE-CREATION <em>HIGHLIGHTS</em></div>
  <div class="brand sm" style="left:314px;top:11px"><span class="brand-dot"></span><span class="brand-name">Vorlanta</span></div>
  <ul class="value-list">
    <li>Sed ut perspiciatis unde omnis iste natus error sit voluptatem accusantium doloremque laudantium, totam rem aperiam, eaque ipsa quae ab illo inventore veritatis</li>
    <li>Sed ut perspiciatis unde omnis iste natus error sit voluptatem accusantium doloremquea.</li>
    <li>Sed ut perspiciatis unde omnis iste natus error sit voluptatem accusantium doloremque laudantium, totam rem aperiam, eaque ipsa quae ab illo inventore veritatis</li>
    <li>Sed ut perspiciatis unde omnis iste natus error sit voluptatem accusantium doloremquea.</li>
    <li>Sed ut perspiciatis unde omnis iste natus error sit voluptatem accusantium doloremque laudantium, totam rem aperiam, eaque ipsa quae ab illo inventore veritatis</li>
    <li>Sed ut perspiciatis unde omnis iste natus error sit voluptatem accusantium doloremquea.</li>
  </ul>
  <div class="photo" style="left:221px;top:49px;width:196px;height:161px;border-radius:8px;background:linear-gradient(140deg,#163e63,#2a6aa0 50%,#0f243a)" role="img" aria-label="Person typing on a laptop with holographic AI interface overlays"></div>
  <div class="footer"><svg class="ico" viewBox="0 0 10 10"><path d="M2 1l2 2-1 1.5a6 6 0 002.5 2.5L7 6l2 2-1.5 1.5C4 9 1 6 .5 2.5z"/></svg>+1 (555) 014 2278 &nbsp;|&nbsp; <svg class="ico" viewBox="0 0 10 10"><rect x="0" y="2" width="10" height="7"/></svg>info@vorlanta.com<span class="page-no">07</span></div>
</section>

<section class="slide col-r row-4" style="background:var(--red-deep)">
  <div class="photo" style="left:0;top:0;width:443px;height:249px;background:radial-gradient(circle at 45% 55%,#c52430,#a20e18 70%)" role="img" aria-label="Faint red background of a light bulb with circuit lines and business icons"></div>
  <div class="brand sm on-red" style="left:314px;top:17px"><span class="brand-dot"></span><span class="brand-name">Vorlanta</span></div>
  <div class="heading" style="left:25px;top:76px;font-size:17px;color:#fff;line-height:1.2">FOR MORE<br>INFORMATION</div>
  <div class="abs" style="left:25px;top:118px;width:28px;height:2px;background:#fff"></div>
  <p class="body-copy" style="left:25px;top:129px;width:180px;color:#f3d6d8;font-size:5.4px">Sed ut perspiciatis unde omnis iste natus error sit voluptatem accusantium doloremque laudantium, totam rem aperiam, eaque ipsa quae ab illo inventore veritatis et quasi architecto beatae vitae dicta sunt explicabo. Nemo enim ipsam voluptatem quia voluptas sit aspernatur aut odit aut fugit, sed quia consequuntur magni dolores eos qui ratione voluptatem sequi nesciunt. Neque porro quisqea.</p>
  <div class="abs" style="left:231px;top:62px;width:1.5px;height:150px;background:#fff"></div>
  <div class="contact-row" style="top:84px"><span class="contact-ico"><svg viewBox="0 0 10 10"><path d="M2 1l2 2-1 1.5a6 6 0 002.5 2.5L7 6l2 2-1.5 1.5C4 9 1 6 .5 2.5z"/></svg></span>+1 (555) 014 2278</div>
  <div class="contact-row" style="top:111px"><span class="contact-ico"><svg viewBox="0 0 10 10"><path d="M0 2h10v6H0z"/><path d="M0 2l5 3.5L10 2" stroke="#fff" stroke-width=".8" fill="none"/></svg></span>info@vorlanta.com</div>
  <div class="contact-row" style="top:136px"><span class="contact-ico"><svg viewBox="0 0 10 10"><path d="M5 0a3.5 3.5 0 013.5 3.5C8.5 6 5 10 5 10S1.5 6 1.5 3.5A3.5 3.5 0 015 0z"/><circle cx="5" cy="3.5" r="1.2" fill="#fff"/></svg></span>218 Marlow Crest Avenue,<br>Suite 40, Dellford</div>
  <div class="contact-row" style="top:163px"><span class="contact-ico"><svg viewBox="0 0 10 10"><circle cx="5" cy="5" r="4.5"/><path d="M.5 5h9M5 .5c-2 2.5-2 6.5 0 9M5 .5c2 2.5 2 6.5 0 9" stroke="#fff" stroke-width=".6" fill="none"/></svg></span>https://vorlanta.com</div>
</section>

</body>
</html>
```